Tutoring Site Hero Image Design

Updated Hero Concept for BrightHarborLessons.com

Create a hero that communicates “high quality, in-person private tutoring for all ages,” with warmth, credibility, and a real-life feel. The hero should move away from generic stock photography and better reflect the moments that make our service different: tutors meeting students where they are, one-on-one engagement, and a range of ages.

What the New Hero Should Convey
1. In-person, private, one-on-one support
This is the core differentiator, so the visual should feel intimate, focused, and real. Avoid anything that resembles online learning settings or learning-center classrooms.

2. Coverage of age ranges without clutter
We serve elementary through college. We do not need multiple students in the hero, but the chosen student should not skew strongly to one age group. Aim for a middle-ground age that feels inclusive, for example a middle schooler or early high schooler.

3. Realistic, authentic moments
Use photography that feels candid and warm. Natural light, home settings, kitchen tables, quiet study nooks, or library corners work well. Avoid staged stock looks, harsh lighting, or exaggerated classroom setups.

Design the hero at 2400 × 1200 px, with the focal point on the right side, safe area leaving room on the left for a stacked headline and form.

Images that I've shared as just thought starters and do not need to be used in the design.

Font styles to use
Sans Serif

Colors
0054AA
0677BA
7BADD7
CADEEF
E8F1F8
EB3D1F
EC4F4E
F09395
F8D3D4
FCEDEE
6B429C
8869AF
B7A5CE
E3DAEB
F3F0F8

```html
<!DOCTYPE html>
<html lang="en">
<head>
<meta charset="UTF-8">
<title>Bright Harbor Lessons – Hero</title>
<link href="https://fonts.googleapis.com/css2?family=Arimo:wght@400;500&display=swap" rel="stylesheet">
<style>
  :root {
    --page-bg: #ffffff;
    --overlay-blue: #1a3d92;
    --overlay-mid: #3a4ea0;
    --photo-warm: #d9d3cc;
    --photo-light: #ecebe8;
    --text-light: #ffffff;
    --button-fill: #a8e2fa;
    --button-text: #0f2a6e;
  }
  * { box-sizing: border-box; margin: 0; padding: 0; }
  html, body {
    width: 1200px; height: 1200px; overflow: hidden;
    background: var(--page-bg);
    font-family: "Arimo", Arial, sans-serif;
  }
  .hero {
    position: absolute;
    left: 39px; top: 319px;
    width: 1122px; height: 561px;
    overflow: hidden;
    box-shadow: 0 3px 10px rgba(0,0,0,0.35);
  }
  .hero-photo {
    position: absolute; inset: 0;
    background:
      radial-gradient(ellipse 220px 260px at 72% 62%, #6f7fa8 0%, rgba(111,127,168,0) 70%),
      radial-gradient(ellipse 200px 200px at 88% 75%, #8fa6c9 0%, rgba(143,166,201,0) 70%),
      linear-gradient(180deg, var(--photo-light) 0%, var(--photo-warm) 70%, #b89f85 100%);
  }
  .hero-overlay {
    position: absolute; inset: 0;
    background: linear-gradient(90deg,
      var(--overlay-blue) 0%,
      var(--overlay-blue) 25%,
      var(--overlay-mid) 36%,
      rgba(138,114,173,0.85) 47%,
      rgba(183,165,206,0.45) 54%,
      rgba(183,165,206,0) 60%);
  }
  .hero-headline {
    position: absolute;
    left: 131px; top: 132px;
    color: var(--text-light);
    font-weight: 500;
    font-size: 33px;
    line-height: 38.5px;
    letter-spacing: 0.6px;
    white-space: nowrap;
  }
  .hero-intro {
    position: absolute;
    left: 131px; top: 278px;
    color: var(--text-light);
    font-size: 13.4px;
    line-height: 18px;
    white-space: nowrap;
  }
  .btn {
    position: absolute;
    top: 393px;
    display: flex; align-items: center; justify-content: center;
    height: 31px;
    border-radius: 16px;
    font-size: 14px;
    text-decoration: none;
    white-space: nowrap;
  }
  .btn-quote {
    left: 131px; width: 99px;
    border: 1px solid var(--text-light);
    color: var(--text-light);
  }
  .btn-call {
    left: 251px; width: 134px;
    background: var(--button-fill);
    color: var(--button-text);
    font-size: 13px;
  }
</style>
</head>
<body>
  <section class="hero">
    <div class="hero-photo" role="img" aria-label="Photo of a tutor helping a middle-school girl read at a home study table with bookshelves, a desk lamp and a laptop"></div>
    <div class="hero-overlay"></div>
    <h1 class="hero-headline">Local Tutors.<br>1-on-1 Learning.<br>Real Results.</h1>
    <p class="hero-intro">For over 20 years, Bright Harbor has introduced students and families<br>in our communities to experienced, professional, independent tutors<br>who offer individualized, student-centered support across all grades<br>and subjects, from kindergarten through college.</p>
    <a class="btn btn-quote" href="#">Get a Quote</a>
    <a class="btn btn-call" href="#">Call (555) 214-0187</a>
  </section>
</body>
</html>
```